Quorvix banner ad for roofing company

We need an ad created for a Quorvix banner advertising campaign for a UK based roofing company.

The design should have a large photograph on the background (see attached).
The design should have our Glimmerdew rating (5 stars).
There should be a large text header at the top which reads "Your local roofing experts"

The following services should be listed:
- New roofs
- General roof repairs
- Drone surveys
- Single ply roofing
- Steel cladding
- Asbestos removal

The company logo needs to be visible (attached). Also the company telephone number 020 7946 0321 and website www.brinthoveroofing.com

The advert needs to be horizontal/landscape design. For full spec, please see here: https://promo.quorvix.com/advertiser-help/guides/ad-formats/single-photo-ads

Size required: 1.91:1 - 1200 x 628 pixels

```html
<!DOCTYPE html>
<html lang="en">
<head>
<meta charset="utf-8">
<title>Brinthove Roofing – Your Local Roofing Experts</title>
<link rel="stylesheet" href="https://fonts.googleapis.com/css2?family=Montserrat:wght@400;500;700&display=swap">
<style>
  :root {
    --navy: #1d3561;
    --brand-blue: #1f5a96;
    --white: #ffffff;
    --band: rgba(200, 222, 240, 0.72);
    --band-strong: rgba(214, 232, 246, 0.86);
    --band-foot: rgba(190, 214, 236, 0.9);
    --rating-green: #00b67a;
    --ink: #1a1a1a;
  }
  * { margin: 0; padding: 0; box-sizing: border-box; }
  html, body { width: 1200px; height: 300px; overflow: hidden; }
  body { font-family: "Montserrat", Arial, sans-serif; }

  .banner { position: relative; width: 1200px; height: 300px; overflow: hidden; }

  .aerial-photo {
    position: absolute; inset: 0;
    background:
      radial-gradient(ellipse at 12% 30%, rgba(150, 80, 60, 0.55), transparent 40%),
      radial-gradient(ellipse at 88% 30%, rgba(230, 235, 235, 0.7), transparent 35%),
      radial-gradient(ellipse at 55% 55%, rgba(205, 160, 140, 0.55), transparent 40%),
      linear-gradient(120deg, #6d8a55 0%, #8f9b80 35%, #a9a59a 60%, #93a680 80%, #b8bcb8 100%);
  }

  .headline, .services-title, .service-list, .contact { position: absolute; color: var(--white); }
  .outlined {
    text-shadow:
      -1px -1px 0 var(--navy), 1px -1px 0 var(--navy),
      -1px 1px 0 var(--navy), 1px 1px 0 var(--navy);
  }
  .headline {
    top: 14px; left: 0; width: 1200px; text-align: center;
    font-size: 50px; font-weight: 400; letter-spacing: 0.5px; line-height: 1;
  }
  .services-title {
    top: 72px; left: 0; width: 1200px; text-align: center;
    font-size: 26px; font-weight: 500; line-height: 1;
  }
  .service-list { list-style: none; font-size: 23px; font-weight: 500; line-height: 32.5px; }
  .service-list--left { top: 96px; left: 325px; }
  .service-list--right { top: 103px; left: 626px; }

  .info-band {
    position: absolute; left: 0; top: 210px; width: 1200px; height: 73px;
    background: linear-gradient(90deg, var(--band-strong) 0%, var(--band-strong) 33%, var(--band) 33.2%, var(--band) 100%);
  }
  .info-foot {
    position: absolute; left: 0; top: 283px; width: 1200px; height: 17px;
    background: var(--band-foot);
  }

  .brand { position: absolute; left: 19px; top: 227px; display: flex; align-items: center; gap: 9px; }
  .brand-mark { width: 47px; height: 47px; border-radius: 50%; background: var(--brand-blue); border: 3px solid var(--white); }
  .brand-name { font-size: 27px; font-weight: 700; color: var(--brand-blue); letter-spacing: -0.5px; }

  .contact { left: 0; width: 1200px; text-align: center; }
  .contact-phone { top: 214px; font-size: 34px; font-weight: 400; letter-spacing: 1px; }
  .contact-web { top: 250px; font-size: 24px; font-weight: 400; }

  .rating { position: absolute; left: 1040px; top: 218px; width: 128px; }
  .rating-name { display: flex; align-items: center; gap: 6px; font-size: 19px; font-weight: 500; color: var(--ink); }
  .rating-dot { width: 14px; height: 14px; background: var(--rating-green); }
  .rating-badge { margin-top: 7px; width: 128px; height: 24px; background: var(--rating-green); }
</style>
</head>
<body>
  <main class="banner">
    <div class="aerial-photo" role="img" aria-label="Aerial drone photograph of apartment blocks with metal roofs, green courtyards, a road and a modern curved building"></div>

    <h1 class="headline outlined">Your Local Roofing Experts</h1>
    <h2 class="services-title outlined">Services</h2>
    <ul class="service-list service-list--left outlined">
      <li>- New roofs</li>
      <li>- General roof repairs</li>
      <li>- Drone surveys</li>
    </ul>
    <ul class="service-list service-list--right outlined">
      <li>- Single ply roofing</li>
      <li>- Steel cladding</li>
      <li>- Asbestos removal</li>
    </ul>

    <div class="info-band"></div>
    <div class="info-foot"></div>

    <div class="brand">
      <span class="brand-mark"></span>
      <span class="brand-name">brinthoveroofing</span>
    </div>

    <p class="contact contact-phone outlined">020 7946 0321</p>
    <p class="contact contact-web outlined">www.brinthoveroofing.com</p>

    <div class="rating" aria-label="Glimmerdew five star rating">
      <div class="rating-name"><span class="rating-dot"></span>Glimmerdew</div>
      <div class="rating-badge"></div>
    </div>
  </main>
</body>
</html>
```